Briloran Clear Springs needs a new business card design (we produce and sell pure bottled water)

We need a clean modern design for our new business cards, We have an existing logo which ultimately cannot be changed, however it could be slighty improved and the colours adjusted. We have this existing logo on all of our bottles, vehicles etc.

Our company slogan is "Clear right to the final sip".
Along with our relevant company information
(Address, phone, website email etc) we will only be using names and not putting position titles for flexibilty.

We are looking for a clean, minimalist modern design.

You can view our website (if need of an update also!) to see our business.

Industry/Entity Type

Business

Contact Information for Business Card

Staff Name : XXXXXX XXXXXX
Address : 9/41 Tavenor St
Halden Rise QLD 4172
Staff Mobile Number : 04XX XXX XXX
Office Phone Number : 07 3918 2457
Staff Email Address : XXXX@brilorancleargo.com.au
Website : www.brilorancleargo.com.au

Font styles to use
Sans Serif

Colors
cee9f5
33a6d7
0492cd
0455a3
3276b5
85abd2
cedeed

Requirements
Must have
• The ability to edit and change the staff members details as we will need to edit for each respective staff member (7 in total)

```html
<!DOCTYPE html>
<html lang="en">
<head>
<meta charset="utf-8">
<title>Briloran Clear Springs – Business Card</title>
<link href="https://fonts.googleapis.com/css2?family=Open+Sans:wght@400;600;700&display=swap" rel="stylesheet">
<style>
  :root {
    --stage-top: #262626;
    --stage-bottom: #050505;
    --card-white: #ffffff;
    --brand-blue: #0455a3;
    --brand-deep: #0a4ea0;
    --rule: #9fb3c8;
    --ink: #1e1e1e;
    --on-blue: #ffffff;
  }
  * { margin: 0; padding: 0; box-sizing: border-box; }
  html, body { width: 1200px; height: 900px; overflow: hidden; }
  body {
    background: linear-gradient(180deg, var(--stage-top) 0%, var(--stage-bottom) 100%);
    font-family: "Open Sans", Arial, sans-serif;
    position: relative;
  }
  .card {
    position: absolute;
    top: 306px;
    width: 440px;
    height: 271px;
    border-radius: 12px;
  }
  .card-front { left: 149px; background: var(--card-white); }
  .card-back { left: 608px; background: var(--brand-blue); }

  .brand-mark {
    position: absolute;
    left: 32px;
    top: 26px;
    width: 150px;
    color: var(--brand-blue);
    font-weight: 700;
    font-size: 21px;
    line-height: 1.1;
    display: flex;
    align-items: center;
    gap: 8px;
  }
  .brand-dot {
    width: 18px; height: 18px; border-radius: 50%;
    background: var(--brand-blue);
    flex: none;
  }
  .staff-name {
    position: absolute;
    left: 30px;
    top: 144px;
    font-size: 15px;
    font-weight: 600;
    color: var(--brand-deep);
  }
  .address {
    position: absolute;
    right: 22px;
    top: 140px;
    text-align: right;
    font-size: 12px;
    line-height: 15px;
    color: var(--ink);
  }
  .divider {
    position: absolute;
    left: 28px; right: 23px; top: 178px;
    height: 1px;
    background: var(--rule);
  }
  .contact-list {
    position: absolute;
    left: 25px;
    top: 183px;
    list-style: none;
    font-size: 12px;
    line-height: 15.7px;
    color: var(--ink);
  }
  .contact-list li { display: flex; align-items: center; gap: 6px; }
  .contact-list svg { width: 9px; height: 9px; fill: var(--brand-blue); flex: none; }

  .back-brand {
    position: absolute;
    left: 0; right: 0; top: 100px;
    text-align: center;
    color: var(--on-blue);
    font-weight: 700;
    font-size: 30px;
    line-height: 1.1;
  }
  .slogan {
    position: absolute;
    left: 0; right: 0; top: 219px;
    text-align: center;
    color: var(--on-blue);
    font-size: 13px;
    font-weight: 600;
    text-transform: uppercase;
  }
</style>
</head>
<body>
  <section class="card card-front">
    <div class="brand-mark"><span class="brand-dot"></span><span>Briloran Clear Springs</span></div>
    <p class="staff-name">Marcus Ellery</p>
    <p class="address">9/41 Tavenor St<br>Halden Rise QLD 4172</p>
    <div class="divider"></div>
    <ul class="contact-list">
      <li><svg viewBox="0 0 10 10"><path d="M3 0h4a1 1 0 0 1 1 1v8a1 1 0 0 1-1 1H3a1 1 0 0 1-1-1V1a1 1 0 0 1 1-1zm0 1.5v6h4v-6zM5 8.2a.5.5 0 1 0 0 1 .5.5 0 0 0 0-1z"/></svg>0400 581 902</li>
      <li><svg viewBox="0 0 10 10"><path d="M2 0l2 2.3-1 1.2a6 6 0 0 0 3.4 3.4l1.2-1L10 8l-1.3 1.6C4.6 10 0 5.4.4 1.3z"/></svg>07 3918 2457</li>
      <li><svg viewBox="0 0 10 10"><path d="M0 2h10v1L5 6 0 3zm0 2l5 3 5-3v4H0z"/></svg>info@brilorancleargo.com.au</li>
      <li><svg viewBox="0 0 10 10"><path d="M5 0a5 5 0 1 0 0 10A5 5 0 0 0 5 0zm-1 2l2 1-1 2 2 1 1 2-3 1-1-3-2-1 1-3z"/></svg>www.brilorancleargo.com.au</li>
    </ul>
  </section>

  <section class="card card-back">
    <div class="back-brand">Briloran<br>Clear Springs</div>
    <p class="slogan">Clear right to the final sip</p>
  </section>
</body>
</html>
```